Design some Business Card for shipping company

We need a creative business card designed for a shipping company. All relevant information such as address and phone number can be found on our website. Will need a design for both front and back. The front will container our logo, slogan, contact information etc. The back will have a coupon and some text. check out www.larvintolfreight.example for all the information. We need something memorable and unique that will stand out. It needs to a horizontal design. Not vertical.

```html
<!DOCTYPE html>
<html lang="en">
<head>
<meta charset="utf-8">
<title>Larvintol Freight – Business Cards</title>
<link href="https://fonts.googleapis.com/css2?family=Poppins:wght@400;600&display=swap" rel="stylesheet">
<style>
  :root {
    --stage: #2b2b2b;
    --card: #ffffff;
    --green: #2f7d4a;
    --green-band: #3a8a57;
    --red: #c8232b;
    --red-band: #c0393f;
    --ink: #1c1c1c;
    --black: #111111;
    --white: #ffffff;
  }
  * { box-sizing: border-box; margin: 0; padding: 0; }
  html, body { width: 1200px; height: 780px; overflow: hidden; }
  body { background: var(--stage); position: relative; font-family: "Poppins", sans-serif; }

  .card {
    position: absolute;
    width: 650px;
    height: 360px;
    background: var(--card);
    overflow: hidden;
    box-shadow: 0 10px 30px rgba(0,0,0,.45);
  }
  .card--front { left: 70px; top: 50px; }
  .card--back { left: 480px; top: 380px; }

  .card__bands { position: absolute; left: 0; bottom: 0; width: 650px; height: 90px; }
  .band-url { font-family: "Poppins", sans-serif; font-weight: 600; font-size: 15px; fill: var(--white); }

  /* Brand: invented name beside one plain circle */
  .brand { position: absolute; display: flex; align-items: center; }
  .brand__dot { border-radius: 50%; background: var(--green); flex: none; }
  .brand__name {
    font-family: "Poppins", sans-serif;
    font-weight: 600;
    color: var(--green);
    line-height: 1;
    white-space: nowrap;
  }

  .card--front .brand { left: 46px; top: 112px; gap: 22px; }
  .card--front .brand__dot { width: 110px; height: 110px; }
  .card--front .brand__name { font-size: 40px; }

  /* Back */
  .card--back .brand { right: 30px; top: 38px; gap: 12px; }
  .card--back .brand__dot { width: 54px; height: 54px; }
  .card--back .brand__name { font-size: 22px; }

  .holder { position: absolute; left: 66px; top: 42px; }
  .holder__name { font-size: 28px; font-weight: 400; color: var(--ink); }
  .holder__role { font-size: 12px; color: var(--ink); margin-left: 52px; }

  .contacts { position: absolute; left: 48px; top: 128px; list-style: none; }
  .contacts li {
    display: flex; align-items: flex-start; gap: 12px;
    font-size: 12.5px; color: var(--ink);
    margin-bottom: 9px; line-height: 1.45;
  }
  .contacts svg { width: 20px; height: 18px; flex: none; margin-top: 1px; }

  .coupon-lines { position: absolute; left: 355px; top: 122px; width: 262px; }
  .coupon-lines span { display: block; height: 3px; background: var(--red); margin-bottom: 13px; }
</style>
</head>
<body>

  <section class="card card--front" aria-label="Front of card">
    <div class="brand">
      <span class="brand__dot"></span>
      <div class="brand__name">Larvintol Freight</div>
    </div>
    <svg class="card__bands" viewBox="0 0 650 90">
      <polygon points="0,66 215,66 191,90 0,90" fill="var(--black)"/>
      <polygon points="240,50 575,22 545,62 205,90" fill="var(--red-band)"/>
      <polygon points="565,40 650,30 650,56 545,66" fill="var(--green-band)"/>
      <text class="band-url" x="252" y="75" transform="rotate(-4.8 252 75)">www.larvintolfreight.example</text>
    </svg>
  </section>

  <section class="card card--back" aria-label="Back of card">
    <div class="brand">
      <span class="brand__dot"></span>
      <div class="brand__name">Larvintol Freight</div>
    </div>

    <div class="holder">
      <div class="holder__name">Mara Lindqvist</div>
      <div class="holder__role">Director</div>
    </div>

    <ul class="contacts">
      <li>
        <svg viewBox="0 0 20 18"><path d="M4 2h4l1 4-2 1.5a9 9 0 0 0 5 5L13.5 10l4 1v4a2 2 0 0 1-2 2A14 14 0 0 1 2 4a2 2 0 0 1 2-2z" fill="var(--red)"/></svg>
        <span>USA: +1 555 014 2290</span>
      </li>
      <li>
        <svg viewBox="0 0 20 18"><path d="M4 2h4l1 4-2 1.5a9 9 0 0 0 5 5L13.5 10l4 1v4a2 2 0 0 1-2 2A14 14 0 0 1 2 4a2 2 0 0 1 2-2z" fill="var(--red)"/></svg>
        <span>KENYA: +254700410822, 0700410822</span>
      </li>
      <li>
        <svg viewBox="0 0 20 18"><rect x="1" y="3" width="18" height="12" fill="var(--red)"/><path d="M1 3l9 7 9-7" fill="none" stroke="#fff" stroke-width="1.5"/></svg>
        <span>info@larvintolfreight.example</span>
      </li>
      <li>
        <svg viewBox="0 0 20 18"><circle cx="10" cy="9" r="8" fill="var(--red)"/><path d="M2 9h16M10 1v16M10 1c-4 4-4 12 0 16M10 1c4 4 4 12 0 16" fill="none" stroke="#fff" stroke-width="1"/></svg>
        <span>www.larvintolfreight.example</span>
      </li>
      <li>
        <svg viewBox="0 0 20 18"><path d="M10 1L1 9h3v8h4v-5h4v5h4V9h3z" fill="var(--red)"/></svg>
        <span>418 Harbor Row NE Ste #12<br>Kirkland WA 98033</span>
      </li>
    </ul>

    <div class="coupon-lines" aria-hidden="true">
      <span></span><span></span><span></span><span></span>
    </div>

    <svg class="card__bands" viewBox="0 0 650 90" aria-hidden="true">
      <polygon points="0,68 250,68 232,90 0,90" fill="var(--black)"/>
      <polygon points="262,62 570,30 545,62 236,90" fill="var(--red-band)"/>
      <polygon points="560,44 650,34 650,60 540,66" fill="var(--green-band)"/>
    </svg>
  </section>

</body>
</html>
```